New Business Card Design Project

Need a design that will create an impact / strong impression towards our clients for our business. We are in the lighting business and we do lighting retrofits for large commercial to industrial clientele.

Target Market(s)

Lighting Industry

Industry/Entity Type

Business

Font styles to use
Other font styles liked:
• we would like to use the font on our logo, not sure what it is though..

Requirements
Must have
• Our logo.
Nice to have
• We are open to suggestions that have to do with lighting.

```html
<!DOCTYPE html>
<html lang="en">
<head>
<meta charset="utf-8">
<title>Lumenway Retrofit Group — Business Card</title>
<link href="https://fonts.googleapis.com/css2?family=Roboto:wght@400;500;700&display=swap" rel="stylesheet">
<style>
  :root {
    --page-bg: #d9dcd8;
    --card-bg: #eef1ee;
    --brand-dark: #1e3a2b;
    --brand-green: #2f8a3c;
    --text-gray: #3b3f3c;
    --band-text: #b9c6bd;
  }
  html, body {
    margin: 0;
    padding: 0;
    width: 1200px;
    height: 969px;
    overflow: hidden;
    background: var(--page-bg);
    font-family: "Roboto", Arial, sans-serif;
  }
  .card {
    position: absolute;
    left: 100px;
    top: 201px;
    width: 1000px;
    height: 566px;
    background: var(--card-bg);
    box-shadow: 0 10px 30px rgba(0,0,0,0.15);
    overflow: hidden;
  }
  .brand {
    position: absolute;
    left: 69px;
    top: 112px;
    display: flex;
    align-items: center;
    gap: 16px;
  }
  .brand-mark {
    width: 26px;
    height: 26px;
    background: var(--brand-green);
    flex: none;
  }
  .brand-name {
    font-weight: 700;
    font-size: 34px;
    line-height: 1;
    color: var(--brand-dark);
    white-space: nowrap;
  }
  .person {
    position: absolute;
    left: 69px;
    top: 316px;
  }
  .person-name {
    font-weight: 500;
    font-size: 35px;
    color: var(--brand-dark);
    line-height: 1.1;
  }
  .person-title {
    font-weight: 700;
    font-size: 24px;
    color: var(--brand-green);
    margin-top: 2px;
  }
  .person-address {
    font-size: 25px;
    color: var(--text-gray);
    line-height: 1.2;
    margin-top: 8px;
  }
  .contacts {
    position: absolute;
    left: 664px;
    top: 318px;
    list-style: none;
    margin: 0;
    padding: 0;
  }
  .contacts li {
    display: flex;
    align-items: center;
    gap: 12px;
    font-size: 25px;
    color: var(--text-gray);
    height: 32px;
    white-space: nowrap;
  }
  .contacts svg {
    width: 20px;
    height: 20px;
    fill: var(--brand-dark);
    flex: none;
  }
  .web-band {
    position: absolute;
    left: 0;
    right: 0;
    top: 500px;
    height: 43px;
    background: var(--brand-dark);
    display: flex;
    align-items: center;
    padding-left: 69px;
  }
  .web-address {
    font-size: 22px;
    color: var(--band-text);
    letter-spacing: 5px;
  }
</style>
</head>
<body>
  <div class="card">
    <div class="brand">
      <span class="brand-mark" aria-hidden="true"></span>
      <span class="brand-name">Lumenway Retrofit Group, LLC.</span>
    </div>

    <div class="person">
      <div class="person-name">DANIEL REYES</div>
      <div class="person-title">CEO/FOUNDER</div>
      <div class="person-address">412 Cedar Hollow Road<br>Boise, Idaho 83702</div>
    </div>

    <ul class="contacts">
      <li>
        <svg viewBox="0 0 24 24" aria-hidden="true"><path d="M6.6 10.8a15.1 15.1 0 0 0 6.6 6.6l2.2-2.2a1 1 0 0 1 1-.25 11.4 11.4 0 0 0 3.6.57 1 1 0 0 1 1 1V20a1 1 0 0 1-1 1A17 17 0 0 1 3 4a1 1 0 0 1 1-1h3.5a1 1 0 0 1 1 1c0 1.25.2 2.45.57 3.6a1 1 0 0 1-.25 1z"/></svg>
        208 555 0147
      </li>
      <li>
        <svg viewBox="0 0 24 24" aria-hidden="true"><path d="M7 1h10a2 2 0 0 1 2 2v18a2 2 0 0 1-2 2H7a2 2 0 0 1-2-2V3a2 2 0 0 1 2-2zm0 4v13h10V5zm5 14.5a1.2 1.2 0 1 0 0 2.4 1.2 1.2 0 0 0 0-2.4z"/></svg>
        208 555 0193
      </li>
      <li>
        <svg viewBox="0 0 24 24" aria-hidden="true"><path d="M7 2h10v5H7zM4 8h16a2 2 0 0 1 2 2v7h-4v5H6v-5H2v-7a2 2 0 0 1 2-2zm4 8v4h8v-4z"/></svg>
        208 555 0162
      </li>
      <li>
        <svg viewBox="0 0 24 24" aria-hidden="true"><path d="M2 5h20v14H2zm2 2v.5l8 5 8-5V7zm0 2.8V17h16V9.8l-8 5z"/></svg>
        daniel@lumenway.com
      </li>
    </ul>

    <div class="web-band">
      <span class="web-address">www.lumenway.com</span>
    </div>
  </div>
</body>
</html>
```